Event Website Design

We need a new website design for an events driven website. The domain for this site is http://brackmoorhalls.co.uk. The site is up and running but needs a new fresh, modern look.
I've attached a Balamiq Mockup for the layout of the home page. Also attached is a png of the logo.
Key colours for the site are 0f7e6a, 35bde, d57835 & 373737.
Font to use is Proxima Nova
Width of the site should be 1200px
The design should be contemporary with minimal clutter.
Websites to references are…
http://vorpin.london/
http://www.darvushall.co.uk/
These are just guidelines, please feel free to use you own creative judgment.
The selected design file needs to be supplied as an editable PSD.
Reason: I've submitted 5 designs to the client, who will select the one they want. I will then choose that design. So please be patient as I'm waiting for a decision from my client.
Industry/Entity Type
Events
Number of Pages Required
1 page
Look and feel
Each slider illustrates characteristics of the customer's brand and the style your logo design should communicate.

```html
<!DOCTYPE html>
<html lang="en">
<head>
<meta charset="utf-8">
<title>Brackmoor Halls – Home</title>
<link rel="stylesheet" href="https://fonts.googleapis.com/css2?family=Figtree:wght@400;600;700&family=Open+Sans:wght@400;600&display=swap">
<style>
:root{
  --dark:#373737;
  --darker:#2f2f2f;
  --blue:#1b5fd9;
  --blue-deep:#1553c0;
  --heading-blue:#1a56c4;
  --teal:#1f9278;
  --orange:#d57835;
  --light:#f0f0f0;
  --card:#efefef;
  --text:#222;
  --muted:#666;
  --foot-text:#bdbdbd;
}
*{box-sizing:border-box;margin:0;padding:0}
html,body{width:1200px;height:2459px;overflow:hidden}
body{font-family:"Figtree",Arial,sans-serif;color:var(--text);background:#fff;position:relative}
.section{position:absolute;left:0;width:1200px}
.wrap{position:relative;width:934px;margin:0 auto;height:100%}
.btn{display:inline-block;height:32px;line-height:32px;padding:0 17px;font-size:10px;font-weight:700;color:#fff;text-transform:uppercase;letter-spacing:.3px;white-space:nowrap}
.btn-more{background:var(--teal)}
.btn-book{background:var(--orange)}
.btn-grey{background:#dedede;color:#333}

/* header */
.site-header{top:0;height:161px;background:var(--dark)}
.brand{position:absolute;left:0;top:58px;color:#fff}
.brand-name{display:flex;align-items:center;gap:9px;font-size:26px;font-weight:700;letter-spacing:1px;white-space:nowrap}
.brand-name .mark{width:16px;height:16px;background:#2bb3a0}
.brand-tag{font-size:8px;color:#ddd;margin-top:8px;white-space:nowrap}
.util-links{position:absolute;right:0;top:22px;font-size:10px;color:#ccc;display:flex;gap:14px;white-space:nowrap}
.util-links span+span::before{content:"|";margin-right:14px;color:#777}
.box-office{position:absolute;right:260px;top:62px;color:#fff;font-size:16px;display:flex;align-items:center;gap:6px;white-space:nowrap}
.search{position:absolute;right:0;top:52px;width:240px;height:40px;background:#fff;display:flex;align-items:center;justify-content:space-between;padding:0 14px;font-size:11px;color:#444}
.socials{position:absolute;right:0;top:111px;display:flex;gap:10px}
.socials i{display:block;width:32px;height:32px}
.s-a{background:#3b5ea8}.s-b{background:#2aa3e8}.s-c{background:var(--orange)}

/* nav */
.main-nav{top:161px;height:44px;background:var(--blue)}
.main-nav ul{list-style:none;display:flex;height:44px}
.main-nav li{flex:0 0 auto;white-space:nowrap;color:#fff;font-size:12.5px;line-height:44px;padding:0 16px}
.main-nav li.active{background:var(--blue-deep);padding:0 24px}

/* hero */
.hero{top:205px;height:410px}
.hero-photo{position:absolute;inset:0;background:linear-gradient(180deg,#3a1a0d 0%,#8a4320 30%,#b86a3a 55%,#8a4a28 72%,#24303a 100%)}
.hero-arrow{position:absolute;top:188px;width:20px;height:34px;background:rgba(0,0,0,.35)}
.hero-caption{position:absolute;left:0;bottom:0;width:934px;height:128px;background:rgba(255,255,255,.92);padding:22px 26px}
.hero-caption h1{font-size:23px;font-weight:700;color:#333}
.hero-caption .date{font-size:14px;margin:6px 0 8px}
.hero-caption p{font-family:"Open Sans",sans-serif;font-size:9.5px;line-height:15px;color:#555;width:700px}
.hero-caption .actions{position:absolute;right:32px;top:76px;display:flex;gap:15px}

/* events */
.events{top:679px;height:280px}
.event-row{display:flex;gap:21px}
.event-card{width:218px;height:280px;background:var(--card)}
.event-card .photo{height:159px}
.event-card h3{font-size:15px;font-weight:700;margin:18px 0 0 14px;white-space:nowrap}
.event-card .date{font-size:11px;margin:6px 0 0 14px}
.event-card .actions{display:flex;gap:13px;margin:14px 0 0 14px}
.car-arrow{position:absolute;top:125px;width:14px;height:28px}
.p1{background:linear-gradient(160deg,#7a4a40,#c9a89a 60%,#5a3a38)}
.p2{background:linear-gradient(160deg,#c79bd8,#f1d6ee 50%,#a766c2)}
.p3{background:linear-gradient(160deg,#3a6a6a,#b89a7a 55%,#4e4a40)}
.p4{background:linear-gradient(160deg,#9a7a68,#d9b8a0 55%,#6a5048)}
.ribbon{position:absolute;left:0;top:50px;width:218px;height:30px;background:rgba(60,60,60,.85);transform:rotate(-22deg);transform-origin:center;color:#fff;font-size:16px;font-weight:600;text-align:center;line-height:30px;letter-spacing:1px;white-space:nowrap}

/* news */
.news{top:1023px;height:344px;background:var(--light)}
.news h2{position:absolute;top:50px;font-size:22px;font-weight:700;color:var(--heading-blue);white-space:nowrap}
.news .see-all{position:absolute;top:81px;left:2px;font-size:10px;color:#333}
.news-row{position:absolute;top:113px;display:flex;gap:20px}
.news-card{width:298px;height:175px;background:#fff;padding:26px 24px}
.news-card h3{font-size:15px;font-weight:700;white-space:nowrap}
.news-card p{font-family:"Open Sans",sans-serif;font-size:9px;line-height:14px;color:#777;margin:10px 0 14px}

/* features */
.features{top:1439px;height:274px}
.feature-row{display:flex;gap:20px}
.feature{width:298px;text-align:center}
.feature svg{height:22px}
.feature h2{font-size:21px;font-weight:700;color:var(--heading-blue);margin:6px 0 12px;white-space:nowrap}
.feature .photo{position:relative;height:199px}
.feature .btn{position:absolute;left:50%;bottom:0;transform:translateX(-50%)}
.f1{background:linear-gradient(135deg,#e4dcc8,#2a3a5a 55%,#e8e0d0)}
.f2{background:linear-gradient(135deg,#8a5a20,#e0b040 50%,#6a3a10)}
.f3{background:linear-gradient(135deg,#3a3a3a,#c8a060 50%,#2a2a2a)}

/* sports banner */
.sports{top:1793px;height:348px;background:linear-gradient(90deg,#d9c9a0,#f3e7c4 40%,#efe3bf 60%,#d8c79d)}
.sports .inner{position:absolute;left:0;top:0;width:100%;text-align:center;padding-top:137px}
.sports h2{font-size:35px;font-weight:700;color:#2a2a2a}
.sports p{font-size:11px;margin-top:6px;color:#333}

/* footer */
.site-footer{top:2141px;height:318px;background:var(--dark)}
.foot-cols{position:absolute;top:60px;display:flex;font-size:10.5px;color:var(--foot-text);line-height:24px;white-space:nowrap}
.foot-cols ul{list-style:none}
.col-addr{width:303px;text-transform:uppercase}
.col-a{width:240px}
.foot-brand{position:absolute;right:0;top:92px;color:#fff;font-size:30px;font-weight:700;letter-spacing:1px;display:flex;align-items:center;gap:10px;white-space:nowrap}
.foot-brand .mark{width:18px;height:18px;background:#8a8a8a}
.foot-rule{position:absolute;left:0;top:239px;width:1200px;height:1px;background:#4a4a4a}
.copyright{position:absolute;left:0;top:270px;width:1200px;text-align:center;font-size:10.5px;color:var(--foot-text)}
</style>
</head>
<body>

<header class="section site-header">
  <div class="wrap">
    <div class="brand">
      <div class="brand-name"><span class="mark"></span>BRACKMOOR HALLS</div>
      <div class="brand-tag">Wessex's Premier Entertainment &amp; Sporting Centre</div>
    </div>
    <div class="util-links"><span>Gift Voucher</span><span>Join Our Mailing List</span><span>My Account</span><span>Basket</span><span>Register</span></div>
    <div class="box-office">
      <svg width="10" height="14" viewBox="0 0 10 14"><rect x="1" y="0.5" width="8" height="13" rx="1.5" fill="none" stroke="#fff" stroke-width="1.4"/><rect x="4" y="10.5" width="2" height="1.4" fill="#fff"/></svg>
      Box Office : 01632 960 418
    </div>
    <div class="search">Search
      <svg width="14" height="14" viewBox="0 0 14 14"><circle cx="6" cy="6" r="4.5" fill="none" stroke="#222" stroke-width="2"/><line x1="9.2" y1="9.2" x2="13" y2="13" stroke="#222" stroke-width="2"/></svg>
    </div>
    <div class="socials"><i class="s-a"></i><i class="s-b"></i><i class="s-c"></i></div>
  </div>
</header>

<nav class="section main-nav">
  <div class="wrap">
    <ul>
      <li class="active">What's On</li><li>Conferencing &amp; Events</li><li>Sports &amp; Leisure</li><li>Lantern Theatre</li><li>Plan Your Visit</li><li>News</li><li>Discover More</li><li>Contact Us</li>
    </ul>
  </div>
</nav>

<section class="section hero">
  <div class="hero-photo" role="img" aria-label="Wood-panelled concert hall stage seen from the seating"></div>
  <span class="hero-arrow" style="left:0"></span>
  <span class="hero-arrow" style="right:0"></span>
  <div class="wrap">
    <div class="hero-caption">
      <h1>Phasellus sem</h1>
      <div class="date">Date : Fri 31st Dec</div>
      <p>Proin congue consectetur metus, et eleifend nisl aliquam sit amet. Fusce odio ex, gravida nec leo ut, condimentum feugiat est. Curabitur porta odio in consectetur sollicitudin. Curabitur bibendum justo massa, eu euismod nibh laoreet quis.</p>
      <div class="actions"><span class="btn btn-more">More</span><span class="btn btn-book">Book</span></div>
    </div>
  </div>
</section>

<section class="section events">
  <svg class="car-arrow" style="left:22px" viewBox="0 0 14 28"><polyline points="12,2 2,14 12,26" fill="none" stroke="#aaa" stroke-width="2"/></svg>
  <svg class="car-arrow" style="right:22px" viewBox="0 0 14 28"><polyline points="2,2 12,14 2,26" fill="none" stroke="#aaa" stroke-width="2"/></svg>
  <div class="wrap">
    <div class="event-row">
      <article class="event-card"><div class="photo p1" role="img" aria-label="Ballet dancers on stage"></div><h3>Sed vel viverra</h3><div class="date">Date : Fri 31st Dec</div><div class="actions"><span class="btn btn-more">More</span><span class="btn btn-book">Book</span></div></article>
      <article class="event-card"><div class="photo p2" role="img" aria-label="Performer in white costume holding a fan"></div><h3>Nam tincidunt lacus</h3><div class="date">Date : Fri 31st Dec</div><div class="actions"><span class="btn btn-more">More</span><span class="btn btn-book">Book</span></div></article>
      <article class="event-card"><div class="photo p3" role="img" aria-label="Costumed cast in a period stage comedy"></div><h3>Nulla semper auctor</h3><div class="date">Date : Fri 31st Dec</div><div class="actions"><span class="btn btn-more">More</span><span class="btn btn-book">Book</span></div></article>
      <article class="event-card"><div class="photo p4" style="position:relative;overflow:hidden" role="img" aria-label="Comedian promotional photo"><div class="ribbon">LIMITED AVAILABILITY</div></div><h3>Aliquam faucibus</h3><div class="date">Date : Fri 31st Dec</div><div class="actions"><span class="btn btn-more">More</span><span class="btn btn-book">Book</span></div></article>
    </div>
  </div>
</section>

<section class="section news">
  <div class="wrap">
    <h2>Latest From Brackmoor</h2>
    <div class="see-all">See All News</div>
    <div class="news-row">
      <article class="news-card"><h3>Integer cursus nulla nec lobortis</h3><p>Proin congue consectetur metus, et eleifend nisl aliquam sit amet. Fusce odio ex, gravida nec leo ut, condimentum feugiat est. Curabitur porta odio in consectetur sollicitudin. Curabitur bibendum justo massa.</p><span class="btn btn-grey">More</span></article>
      <article class="news-card"><h3>Integer cursus nulla nec lobortis</h3><p>Proin congue consectetur metus, et eleifend nisl aliquam sit amet. Fusce odio ex, gravida nec leo ut, condimentum feugiat est. Curabitur porta odio in consectetur sollicitudin. Curabitur bibendum justo massa.</p><span class="btn btn-grey">More</span></article>
      <article class="news-card"><h3>Integer cursus nulla nec lobortis</h3><p>Proin congue consectetur metus, et eleifend nisl aliquam sit amet. Fusce odio ex, gravida nec leo ut, condimentum feugiat est. Curabitur porta odio in consectetur sollicitudin. Curabitur bibendum justo massa.</p><span class="btn btn-grey">More</span></article>
    </div>
  </div>
</section>

<section class="section features">
  <div class="wrap">
    <div class="feature-row">
      <div class="feature">
        <svg viewBox="0 0 28 22" width="28"><circle cx="14" cy="6" r="4" fill="#1a56c4"/><circle cx="6" cy="8" r="3" fill="#1a56c4"/><circle cx="22" cy="8" r="3" fill="#1a56c4"/><path d="M7 21a7 7 0 0 1 14 0z" fill="#1a56c4"/><path d="M0 20a6 6 0 0 1 7-5.5 9 9 0 0 0-2 5.5z M28 20a6 6 0 0 0-7-5.5 9 9 0 0 1 2 5.5z" fill="#1a56c4"/></svg>
        <h2>Conference &amp; Events</h2>
        <div class="photo f1" role="img" aria-label="Speaker presenting at a lectern"><span class="btn btn-more">More</span></div>
      </div>
      <div class="feature">
        <svg viewBox="0 0 20 22" width="20"><path d="M1 1h18l-7.5 9v8h4v3h-11v-3h4v-8z" fill="#1a56c4"/></svg>
        <h2>Parties at Brackmoor</h2>
        <div class="photo f2" role="img" aria-label="Wine glasses raised in a toast"><span class="btn btn-more">More</span></div>
      </div>
      <div class="feature">
        <svg viewBox="0 0 28 22" width="28"><path d="M2 2h15v10h-8l-5 4v-4h-2z" fill="#1a56c4"/><path d="M19 6h7v10h-2v4l-5-4h-7v-2h7z" fill="#1a56c4"/></svg>
        <h2>Co-working Hub</h2>
        <div class="photo f3" role="img" aria-label="Colleagues chatting over coffee at a counter"><span class="btn btn-more">More</span></div>
      </div>
    </div>
  </div>
</section>

<section class="section sports" role="img" aria-label="Group stretching in a bright fitness studio">
  <div class="inner">
    <h2>Sports &amp; Leisure</h2>
    <p>Click here for read more</p>
  </div>
</section>

<footer class="section site-footer">
  <div class="wrap">
    <div class="foot-cols">
      <ul class="col-addr"><li>Brackmoor Entertainment Venue</li><li>Harrow Lane</li><li>Brackmoor</li><li>Wessex</li><li>BM4 7QX</li></ul>
      <ul class="col-a"><li>What's On</li><li>Conferencing &amp; Events</li><li>Sports &amp; Leisure</li><li>Lantern Theatre</li></ul>
      <ul><li>Plan Your Visit</li><li>News</li><li>Discover More</li><li>Contact Us</li></ul>
    </div>
    <div class="foot-brand"><span class="mark"></span>BRACKMOOR</div>
  </div>
  <div class="foot-rule"></div>
  <div class="copyright">Copyright &copy; 2016 Company name. All rights reserved.</div>
</footer>

</body>
</html>
```